Stationery Set for Velmora Company

I need to create full stationery design for my company; Business Cards, Envelops, Letter Heads, Calendar.
In the letter head and Envelops... only contact information and website links.
Our company is a Service Management company with different domains of innovative services including Technology Service Management, Education Services, Outsourcing Management, Events Management.
I need a modern and innovative design specially for the business card. I some transparent designs and I like it, but don't limit your innovation to what I mentioned. Sky is limit for your innovation.

Target Market(s)

Middle East & Africa

Industry/Entity Type

Business Management

Colors
34a7d8
0355a3
85acd3
86cae7
cee9f5
cfdeed
e4daeb
f3f1f8
ecf7fb

Requirements
Must have
• Name, Title, Email, Mobile
Nice to have
• We have multiple locations in USA, KSA, EGY, so I need ideas about how to include all contact details maybe QR / Barcode or something else.
• Please see our locations and contact information: www.brightvelmora.example
Should not have
• Too much text

```html
<!DOCTYPE html>
<html lang="en">
<head>
<meta charset="UTF-8">
<title>Velmora Company – Business Card</title>
<link href="https://fonts.googleapis.com/css2?family=Roboto:wght@400;500&display=swap" rel="stylesheet">
<style>
  :root {
    --backdrop: #2b2b2d;
    --paper: #ffffff;
    --brand-blue: #4a7cc6;
    --ink-dark: #222428;
    --ink-light: #ffffff;
  }
  * { margin: 0; padding: 0; box-sizing: border-box; }
  html, body {
    width: 1200px; height: 750px; overflow: hidden;
    background: var(--backdrop);
    font-family: "Roboto", Arial, sans-serif;
  }
  .stage {
    position: relative; width: 1200px; height: 750px;
    display: flex; align-items: center; justify-content: center; gap: 50px;
  }
  .card {
    position: relative; width: 525px; height: 300px;
    background: var(--paper); overflow: hidden;
    box-shadow: 0 14px 30px rgba(0,0,0,.45);
  }
  .wordmark {
    display: flex; align-items: center; gap: 10px;
    color: var(--brand-blue); font-weight: 500; font-size: 44px; letter-spacing: 1px;
  }
  .wordmark__dot {
    width: 16px; height: 16px; border-radius: 50%; background: var(--brand-blue);
  }
  /* front */
  .card--front { display: flex; flex-direction: column; align-items: center; justify-content: center; }
  .card--front .wordmark { margin-top: -10px; }
  .card--front .website {
    margin-top: 38px; font-size: 14px; letter-spacing: 2px; color: var(--ink-dark);
  }
  /* back */
  .card--back .identity {
    position: absolute; left: 0; top: 0; width: 270px; height: 100%;
    display: flex; flex-direction: column; align-items: center; justify-content: center;
  }
  .card--back .wordmark { font-size: 36px; }
  .person-name {
    margin-top: 26px; color: var(--brand-blue); font-weight: 500; font-size: 20px; letter-spacing: .5px;
  }
  .person-title { margin-top: 4px; color: var(--ink-dark); font-size: 15px; }
  .contact-panel {
    position: absolute; right: 0; top: 0; width: 270px; height: 100%;
    background: var(--brand-blue); border-radius: 40px 0 0 40px;
    color: var(--ink-light); font-size: 12.5px; line-height: 1.4;
    padding: 22px 20px 22px 18px; text-align: right;
    display: flex; flex-direction: column; justify-content: center; gap: 12px;
  }
  .contact-line { display: flex; justify-content: flex-end; align-items: center; gap: 6px; }
  .contact-line svg { width: 13px; height: 13px; flex: none; fill: var(--ink-light); }
</style>
</head>
<body>
<main class="stage">
  <section class="card card--front">
    <div class="wordmark"><span class="wordmark__dot"></span>Velmora</div>
    <p class="website">www.brightvelmora.example</p>
  </section>

  <section class="card card--back">
    <div class="identity">
      <div class="wordmark"><span class="wordmark__dot"></span>Velmora</div>
      <p class="person-name">OMAR NASSER</p>
      <p class="person-title">President</p>
    </div>
    <div class="contact-panel">
      <address class="office" style="font-style:normal">
        48 Harbor Crest Road<br>4th Floor Lindale City<br>CA 90000 US
        <span class="contact-line">+1.5550102040
          <svg viewBox="0 0 16 16"><path d="M2 5c0-2 3-3 6-3s6 1 6 3v1h-3V4.5H5V6H2zM3 7h10l1 7H2zm5 2a2 2 0 100 4 2 2 0 000-4z"/></svg>
        </span>
      </address>
      <address class="office" style="font-style:normal">
        Riyadh, Al Nakheel<br>Qasr Al Noor St<br>Noor Plaza Buildings<br>Block 3C 1st Floor A12, A14
        <span class="contact-line">+966 55500 11 40
          <svg viewBox="0 0 16 16"><path d="M2 5c0-2 3-3 6-3s6 1 6 3v1h-3V4.5H5V6H2zM3 7h10l1 7H2zm5 2a2 2 0 100 4 2 2 0 000-4z"/></svg>
        </span>
      </address>
      <div class="direct">
        <span class="contact-line">+1.5550102040
          <svg viewBox="0 0 16 16"><path d="M4 1h8v14H4zm1.5 1.5v9h5v-9zM8 12.3a.8.8 0 100 1.6.8.8 0 000-1.6z"/></svg>
        </span>
        <span class="contact-line">info@brightvelmora.example
          <svg viewBox="0 0 16 16"><path d="M1 3h14v10H1zm1.5 1.5v.4L8 9l5.5-4.1v-.4zm0 2.3v4.7h11V6.8L8 10.9z"/></svg>
        </span>
      </div>
    </div>
  </section>
</main>
</body>
</html>
```